Corwin Ashby College of Nursing website

Nursing college needs a fresh, streamlined website. Many of the items on our website are required by accreditation organizations.

```html
<!DOCTYPE html>
<html lang="en">
<head>
<meta charset="utf-8">
<title>Corwin Ashby College of Nursing</title>
<link rel="stylesheet" href="https://fonts.googleapis.com/css2?family=Playfair+Display:wght@700&family=Poppins:wght@400;500;600&display=swap">
<style>
:root{
  --navy:#0d3e66;
  --navy-dark:#0b3458;
  --purple:#6b1f6f;
  --ink:#2b2b2b;
  --muted:#444;
  --band:#eef0f3;
  --white:#fff;
}
*{box-sizing:border-box;margin:0;padding:0}
html,body{width:1200px;height:3800px;overflow:hidden}
body{position:relative;background:var(--white);font-family:"Poppins",sans-serif;color:var(--ink)}
.abs{position:absolute}
.serif{font-family:"Playfair Display",serif;font-weight:700;text-transform:uppercase;letter-spacing:1px}
.btn{position:absolute;display:flex;align-items:center;justify-content:center;border-radius:20px;font-weight:500;font-size:15px;text-transform:uppercase}
.btn-navy{background:var(--navy);color:#fff}
.btn-outline{border:1.5px solid var(--navy);color:var(--navy);background:#fff}

/* header */
.site-header{position:absolute;left:0;top:0;width:1200px;height:95px;background:#fff}
.phone-pill{left:140px;top:15px;width:158px;height:32px;background:var(--navy);color:#fff;border-radius:16px;font-size:14px;display:flex;align-items:center;gap:10px;padding-left:18px}
.search-pill{left:918px;top:15px;width:158px;height:32px;background:var(--navy);color:#cfdbe6;border-radius:16px;font-size:11px;display:flex;align-items:center;gap:10px;padding-left:18px}
.nav{top:64px;font-size:13px;color:#444;text-transform:uppercase;display:flex;gap:28px}
.nav .active{color:var(--purple);border-bottom:1px solid var(--purple)}
.brand-seal{left:530px;top:12px;width:140px;height:140px;border-radius:50%;background:#fff;border:4px solid var(--purple);display:flex;align-items:center;justify-content:center;text-align:center;color:var(--navy);font-size:13px;font-weight:600;line-height:1.35;padding:18px;z-index:3}

/* hero */
.hero{position:absolute;left:0;top:95px;width:1200px;height:520px;overflow:hidden}
.hero-bg{position:absolute;inset:0;background:linear-gradient(90deg,#0a3256 0%,#0f4a78 55%,#1a5f91 100%)}
.hero-photo{position:absolute;left:620px;top:30px;width:420px;height:440px;background:radial-gradient(ellipse at 55% 45%,#3fb2cf 0%,#1e7fa7 45%,rgba(15,74,120,0) 75%)}
.hero h1{left:146px;top:100px;color:#fff;font-size:34px;line-height:60px}
.hero p{left:146px;top:225px;width:470px;color:#fff;font-size:15px;line-height:34px}
.hero .btn{top:350px;height:40px}
.social{left:34px;top:80px;display:flex;flex-direction:column;gap:10px}
.social span{width:16px;height:16px;border:1.5px solid #fff;border-radius:50%}
.scroll-line{left:41px;top:196px;width:1px;height:80px;background:#fff}
.scroll-text{left:26px;top:385px;color:#fff;font-size:11px;transform:rotate(-90deg);transform-origin:left top;letter-spacing:1px}

/* about */
.seal-large{left:115px;top:703px;width:390px;height:390px;border-radius:50%;border:4px solid var(--purple);display:flex;align-items:center;justify-content:center;text-align:center;color:var(--navy);font-size:34px;font-weight:600;line-height:1.3;padding:50px}
.about-body{left:612px;top:690px;width:490px;display:flex;flex-direction:column;align-items:flex-start}
.about-body h2{font-size:28px;color:var(--navy);line-height:44px}
.about-body p{margin-top:14px;font-size:14px;line-height:34px;color:var(--muted)}
.about-body .btn{position:static;margin-top:18px;width:148px;height:38px}

/* services */
.services{position:absolute;left:0;top:1173px;width:1200px;height:917px;background:var(--band);overflow:hidden}
.services h2{left:114px;top:100px;font-size:30px;line-height:59px;color:var(--navy)}
.services .rule{left:114px;top:285px;width:140px;height:3px;background:var(--navy)}
.card{position:absolute;width:301px;height:395px;background:#fff;box-shadow:0 2px 8px rgba(0,0,0,.06);text-align:center;padding:28px 16px 0}
.card .icon{width:80px;height:80px;margin:0 auto;border:1.5px dashed var(--navy);border-radius:50%;display:flex;align-items:center;justify-content:center}
.card h3{margin-top:20px;font-size:22px;line-height:38px;color:var(--navy)}
.card p{margin-top:8px;font-size:13px;line-height:31px;color:var(--muted)}
.card .btn{left:90px;bottom:36px;width:122px;height:30px;font-size:12.5px}
.card-photo{background:linear-gradient(160deg,#1d4e7a 0%,#123a62 60%,#0b2d4f 100%)}
.card-photo h3,.card-photo p{color:#fff}
.card-photo .icon{border-color:#fff}
.card-photo .btn{background:#fff;color:var(--navy)}

/* process */
.process h2{left:0;width:1200px;top:2165px;text-align:center;font-size:30px;color:var(--navy)}
.step{position:absolute;width:240px;text-align:center}
.step svg{display:block;margin:0 auto}
.step h3{font-size:21px;color:var(--navy)}
.step.purple h3{color:var(--purple)}
.step p{margin:10px auto 0;width:220px;font-size:14px;line-height:28px;color:var(--muted)}
.step p.narrow{width:180px}

/* news */
.news{position:absolute;left:0;top:2805px;width:1200px;height:590px;background:var(--band)}
.news h2{left:0;width:1200px;top:55px;text-align:center;font-size:30px;color:var(--navy)}
.post{position:absolute;top:137px;width:315px;text-align:center}
.post .media{width:315px;height:250px}
.post .kicker{margin-top:32px;font-size:16px;color:var(--navy);text-transform:uppercase;line-height:30px}
.post .title{font-size:16px;color:#222;text-transform:uppercase;line-height:32px}
.post .btn{position:relative;margin:12px auto 0;width:120px;height:33px;font-size:14px}
.arrow{position:absolute;top:253px;width:24px;height:24px;border-radius:50%;background:var(--navy);display:flex;align-items:center;justify-content:center}

/* footer */
.site-footer{position:absolute;left:0;top:3395px;width:1200px;height:405px;background:var(--navy-dark);color:#fff}
.seal-footer{left:88px;top:70px;width:200px;height:200px;border-radius:50%;border:3px solid #fff;display:flex;align-items:center;justify-content:center;text-align:center;font-size:18px;font-weight:600;line-height:1.3;padding:26px}
.site-footer h4{font-size:17px;font-weight:500;text-transform:uppercase}
.links{list-style:none;font-size:13px;text-transform:uppercase}
.links li{height:40px;padding-left:16px;position:relative}
.links li::before{content:"";position:absolute;left:0;top:7px;width:5px;height:5px;border-radius:50%;background:#fff}
.contact-row{position:absolute;left:864px;display:flex;gap:16px;font-size:13px;line-height:26px;text-transform:uppercase}
.badge{position:absolute;width:54px;height:54px;border-radius:50%;background:#fff;border:3px solid #1f1f3a}
.divider{left:65px;top:338px;width:1070px;height:1px;background:#5a7c9c}
.copyright{left:0;width:1200px;top:360px;text-align:center;font-size:14px}
</style>
</head>
<body>

<header class="site-header">
  <div class="abs phone-pill">
    <svg width="14" height="14" viewBox="0 0 24 24"><path fill="#fff" d="M6.6 10.8a15 15 0 0 0 6.6 6.6l2.2-2.2a1 1 0 0 1 1-.25 11 11 0 0 0 3.6.6 1 1 0 0 1 1 1V20a1 1 0 0 1-1 1A17 17 0 0 1 3 4a1 1 0 0 1 1-1h3.5a1 1 0 0 1 1 1 11 11 0 0 0 .6 3.6 1 1 0 0 1-.25 1z"/></svg>
    212-555-0148
  </div>
  <nav class="abs nav" style="left:139px">
    <span class="active">Home</span><span>About</span><span>Academics</span><span>Library</span>
  </nav>
  <div class="abs brand-seal">Corwin Ashby College of Nursing</div>
  <div class="abs search-pill">
    <svg width="13" height="13" viewBox="0 0 24 24"><circle cx="10" cy="10" r="7" fill="none" stroke="#fff" stroke-width="2.5"/><path d="M15 15l6 6" stroke="#fff" stroke-width="2.5"/></svg>
    SEARCH HERE
  </div>
  <nav class="abs nav" style="left:698px">
    <span>Policies &amp; Handbooks</span><span>Contact Us</span><span>Donate</span>
  </nav>
</header>

<section class="hero">
  <div class="hero-bg" role="img" aria-label="College building exterior in deep blue tones"></div>
  <div class="hero-photo" role="img" aria-label="Smiling nursing student in teal scrubs holding a tablet"></div>
  <div class="abs social"><span></span><span></span><span></span><span></span></div>
  <div class="abs scroll-line"></div>
  <div class="abs scroll-text">SCROLL DOWN</div>
  <h1 class="abs serif">Empowering Future Nurses<br>With Excellence</h1>
  <p class="abs">Corwin Ashby College of Nursing. Corwin Ashby College of Nursing has been educating nurses for over seventy years. Founded in 1945</p>
  <div class="btn" style="left:146px;width:148px;background:#fff;color:var(--navy)">Apply Now</div>
  <div class="btn" style="left:309px;width:148px;border:1.5px solid #fff;color:#fff">Request Info</div>
  <svg class="abs" style="left:0;bottom:0" width="1200" height="110" viewBox="0 0 1200 110">
    <path d="M0 0 Q600 120 1200 20 L1200 110 L0 110Z" fill="#fff"/>
    <path d="M0 30 Q600 150 1200 20" fill="none" stroke="#0d3e66" stroke-width="8"/>
  </svg>
</section>

<section class="about">
  <div class="abs seal-large">Corwin Ashby College of Nursing</div>
  <div class="abs about-body">
    <h2 class="serif">About the College</h2>
    <p>The Corwin Ashby College of Nursing (CACN) was founded in 1945 as a private, non-profit College, and is at the forefront of nursing education. Accredited by NANA (for the AAS program), CNEB (for the BS programs) and Central States (for the entire College),<br>The Corwin Ashby College of Nursing (CACN) was founded in 1945 as a private, non-profit College, and is at the forefront of nursing education. Accredited by NANA (for the AAS program), CNEB (for the BS programs) and Central States (for the entire College).</p>
    <div class="btn btn-navy">Read More</div>
  </div>
</section>

<section class="services">
  <h2 class="abs serif">Get the level<br>of service<br>you deserve</h2>
  <div class="abs rule"></div>

  <article class="card" style="left:453px;top:52px">
    <div class="icon"><svg width="40" height="40" viewBox="0 0 40 40" fill="none" stroke="#0d3e66" stroke-width="2"><path d="M6 12h12v20H6zM22 12h12v20H22z"/><circle cx="20" cy="7" r="3" stroke="#6b1f6f"/></svg></div>
    <h3 class="serif">Education</h3>
    <p>The faculty believe that education is a dynamic, ongoing process that aims to stimulate intellectual curiosity and to help each individual</p>
    <div class="btn btn-navy">Read More</div>
  </article>

  <article class="card card-photo" style="left:787px;top:52px" role="img" aria-label="Nurse caring for an elderly patient">
    <div class="icon"><svg width="40" height="40" viewBox="0 0 40 40" fill="none" stroke="#fff" stroke-width="2"><circle cx="13" cy="14" r="4"/><circle cx="27" cy="14" r="4"/><path d="M6 32c0-6 3-10 7-10s7 4 7 10M20 32c0-6 3-10 7-10s7 4 7 10"/></svg></div>
    <h3 class="serif">Nursing</h3>
    <p>Nursing is the science and practice that promotes a person's adaptation to achieve integration with his/her environment during health and illness.</p>
    <div class="btn">Read More</div>
  </article>

  <article class="card" style="left:111px;top:472px">
    <div class="icon"><svg width="40" height="40" viewBox="0 0 40 40" fill="none" stroke="#0d3e66" stroke-width="2"><circle cx="20" cy="16" r="8" stroke="#6b1f6f"/><path d="M6 28c6 0 10 4 14 4s8-4 14-4"/></svg></div>
    <h3 class="serif">Environment</h3>
    <p>Environment is defined as all conditions, circumstances, and influences surrounding and affecting the development</p>
    <div class="btn btn-navy">Read More</div>
  </article>

  <article class="card" style="left:453px;top:472px">
    <div class="icon"><svg width="40" height="40" viewBox="0 0 40 40" fill="none" stroke="#0d3e66" stroke-width="2"><rect x="8" y="7" width="18" height="26"/><path d="M12 14h10M12 20h8"/><path d="M22 26l4-4 3 3 5-5" stroke="#6b1f6f"/></svg></div>
    <h3 class="serif">Health</h3>
    <p>Health is defined as a state and a process of being and becoming an integrated and whole human being. Health is a reflection</p>
    <div class="btn btn-navy">Read More</div>
  </article>

  <article class="card" style="left:787px;top:472px">
    <div class="icon"><svg width="40" height="40" viewBox="0 0 40 40" fill="none" stroke="#0d3e66" stroke-width="2"><circle cx="20" cy="14" r="6"/><path d="M9 34c0-7 5-11 11-11s11 4 11 11"/><path d="M20 26v5M17.5 28.5h5" stroke="#6b1f6f"/></svg></div>
    <h3 class="serif">Licensed Practical Nurse</h3>
    <p>The licensed practical nurse, under the direction of a registered nurse, is prepared to give basic nursing care.</p>
    <div class="btn btn-navy">Read More</div>
  </article>
</section>

<section class="process">
  <h2 class="abs serif">Our Process</h2>

  <div class="step" style="left:108px;top:2240px">
    <svg width="240" height="230" viewBox="0 0 240 230">
      <circle cx="120" cy="115" r="75" fill="#fff" stroke="#eceff2" stroke-width="6"/>
      <path d="M15 115 A105 105 0 0 1 225 115" fill="none" stroke="#0d3e66" stroke-width="8"/>
      <circle cx="18" cy="118" r="15" fill="#0d3e66"/><text x="18" y="123" fill="#fff" font-size="14" text-anchor="middle" font-family="Poppins,sans-serif">1</text>
      <g fill="none" stroke="#0d3e66" stroke-width="2.5"><rect x="98" y="85" width="40" height="52"/><path d="M106 98h14M106 108h22M106 118h16"/><circle cx="136" cy="128" r="9"/><path d="M142 134l8 8"/></g>
    </svg>
    <h3 class="serif">Apply Now</h3>
    <p class="narrow">Generic BS Program (No LPN/clinical background required)</p>
  </div>

  <div class="step purple" style="left:359px;top:2318px">
    <svg width="240" height="230" viewBox="0 0 240 230">
      <circle cx="120" cy="115" r="75" fill="#fff" stroke="#eceff2" stroke-width="6"/>
      <path d="M15 115 A105 105 0 0 0 225 115" fill="none" stroke="#6b1f6f" stroke-width="8"/>
      <circle cx="18" cy="112" r="15" fill="#6b1f6f"/><text x="18" y="117" fill="#fff" font-size="14" text-anchor="middle" font-family="Poppins,sans-serif">2</text>
      <g fill="none" stroke="#6b1f6f" stroke-width="2.5"><circle cx="120" cy="95" r="10"/><circle cx="102" cy="122" r="6"/><circle cx="120" cy="120" r="6"/><circle cx="138" cy="122" r="6"/><path d="M92 142c0-8 20-8 20 0M110 142c0-8 20-8 20 0M128 142c0-8 20-8 20 0"/></g>
    </svg>
    <h3 class="serif">Our Successes</h3>
    <p>CACN is an independent single-purpose institution. Its mission is to provide a dynamic</p>
  </div>

  <div class="step" style="left:611px;top:2240px">
    <svg width="240" height="230" viewBox="0 0 240 230">
      <circle cx="120" cy="115" r="75" fill="#fff" stroke="#eceff2" stroke-width="6"/>
      <path d="M15 115 A105 105 0 0 1 225 115" fill="none" stroke="#0d3e66" stroke-width="8"/>
      <circle cx="18" cy="118" r="15" fill="#0d3e66"/><text x="18" y="123" fill="#fff" font-size="14" text-anchor="middle" font-family="Poppins,sans-serif">3</text>
      <g fill="none" stroke="#0d3e66" stroke-width="2.5"><circle cx="120" cy="125" r="18"/><circle cx="104" cy="96" r="6"/><circle cx="120" cy="92" r="6"/><circle cx="136" cy="96" r="6"/><path d="M96 112c0-6 16-6 16 0M112 108c0-6 16-6 16 0M128 112c0-6 16-6 16 0"/></g>
    </svg>
    <h3 class="serif">Demographics</h3>
    <p>Student Demographics<br>Graduating Students</p>
  </div>

  <div class="step purple" style="left:862px;top:2318px">
    <svg width="240" height="230" viewBox="0 0 240 230">
      <circle cx="120" cy="115" r="75" fill="#fff" stroke="#eceff2" stroke-width="6"/>
      <path d="M15 115 A105 105 0 0 0 225 115" fill="none" stroke="#6b1f6f" stroke-width="8"/>
      <circle cx="18" cy="112" r="15" fill="#6b1f6f"/><text x="18" y="117" fill="#fff" font-size="14" text-anchor="middle" font-family="Poppins,sans-serif">4</text>
      <g fill="none" stroke="#6b1f6f" stroke-width="2.5"><circle cx="126" cy="100" r="14"/><path d="M126 99v8"/><path d="M96 128h12l10 4h12c4 0 4 6 0 6h-14M96 124v20"/></g>
    </svg>
    <h3 class="serif">Information</h3>
    <p>State Board RN Pass Rate Consumer Information Contact Information AAS Course Information</p>
  </div>

  <div class="btn btn-navy" style="left:517px;top:2700px;width:166px;height:38px">Find Out More</div>
</section>

<section class="news">
  <h2 class="abs serif">News &amp; Updates</h2>
  <div class="arrow" style="left:43px"><svg width="10" height="10" viewBox="0 0 10 10"><path d="M7 1L3 5l4 4" fill="none" stroke="#fff" stroke-width="2"/></svg></div>
  <div class="arrow" style="left:1126px"><svg width="10" height="10" viewBox="0 0 10 10"><path d="M3 1l4 4-4 4" fill="none" stroke="#fff" stroke-width="2"/></svg></div>

  <article class="post" style="left:111px">
    <div class="media" role="img" aria-label="Open house flyer with a smiling nursing student" style="background:linear-gradient(180deg,#7d3fb0 0%,#9c72cf 100%)"></div>
    <div class="kicker">CACN Open House</div>
    <div class="title">CACN January 2024 Open[...]</div>
    <div class="btn btn-outline">Read More</div>
  </article>

  <article class="post" style="left:443px">
    <div class="media" role="img" aria-label="Pink entrance exams announcement with checklist" style="background:linear-gradient(180deg,#e88aa6 0%,#dc7396 100%)"></div>
    <div class="kicker">Now Accepting Pre-Entrance<br>Exams!</div>
    <div class="btn btn-outline">Read More</div>
  </article>

  <article class="post" style="left:774px">
    <div class="media" role="img" aria-label="Student writing with a pen beside a coffee cup" style="background:linear-gradient(160deg,#d9d6d0 0%,#a9a39b 60%,#6f6861 100%)"></div>
    <div class="kicker">Upcoming Entrance Testing</div>
    <div class="title">Pre-Admission Testing</div>
    <div class="btn btn-outline">Read More</div>
  </article>
</section>

<footer class="site-footer">
  <div class="abs seal-footer">Corwin Ashby College of Nursing</div>

  <h4 class="abs" style="left:365px;top:62px">Quick Links</h4>
  <ul class="abs links" style="left:365px;top:110px">
    <li>Office Hub</li><li>Coursebay LMS</li><li>Ledgerline Portal</li><li>Email</li><li>Apex Testing</li>
  </ul>
  <ul class="abs links" style="left:597px;top:110px">
    <li>Proctorly</li><li>Hartwell Connect</li><li>PayDesk (Employees Only)</li><li>Payline Flex (Staff Only)</li><li>Veridian SIS</li>
  </ul>

  <h4 class="abs" style="left:864px;top:62px">Contact Us</h4>
  <div class="contact-row" style="top:106px">
    <svg width="20" height="20" viewBox="0 0 24 24"><path fill="#fff" d="M12 2a7 7 0 0 0-7 7c0 5 7 13 7 13s7-8 7-13a7 7 0 0 0-7-7zm0 9.5A2.5 2.5 0 1 1 12 6.5a2.5 2.5 0 0 1 0 5z"/></svg>
    <span>180 Linden Row<br>New York, NY 10027</span>
  </div>
  <div class="contact-row" style="top:172px">
    <svg width="20" height="20" viewBox="0 0 24 24"><circle cx="12" cy="12" r="11" fill="#fff"/><path fill="#0b3458" d="M8.5 10.2a8 8 0 0 0 4.3 4.3l1.4-1.4a.7.7 0 0 1 .7-.2 6 6 0 0 0 2 .3.6.6 0 0 1 .6.6v2a.6.6 0 0 1-.6.6A10 10 0 0 1 6 6.6.6.6 0 0 1 6.6 6h2a.6.6 0 0 1 .6.6 6 6 0 0 0 .3 2 .7.7 0 0 1-.2.7z"/></svg>
    <span>(212) 555-0190/0191</span>
  </div>
  <div class="contact-row" style="top:212px">
    <svg width="20" height="20" viewBox="0 0 24 24"><circle cx="12" cy="12" r="11" fill="#fff"/><rect x="6.5" y="8" width="11" height="8" fill="none" stroke="#0b3458" stroke-width="1.5"/><path d="M6.5 8l5.5 4.5L17.5 8" fill="none" stroke="#0b3458" stroke-width="1.5"/></svg>
    <span>registrar@corwinashby.edu</span>
  </div>
  <div class="badge" style="left:866px;top:261px"></div>
  <div class="badge" style="left:939px;top:261px;background:#1f1f3a;border-color:#fff"></div>

  <svg class="abs" style="left:1108px;top:292px" width="44" height="44" viewBox="0 0 44 44">
    <rect x="12" y="4" width="26" height="18" rx="4" fill="#fff"/>
    <rect x="4" y="16" width="26" height="18" rx="4" fill="none" stroke="#fff" stroke-width="2.5"/>
    <circle cx="12" cy="25" r="2" fill="#fff"/><circle cx="17" cy="25" r="2" fill="#fff"/><circle cx="22" cy="25" r="2" fill="#fff"/>
  </svg>

  <div class="abs divider"></div>
  <div class="abs copyright">@2024 COPYRIGHTS - ALL RIGHTS RESERVED</div>
</footer>

</body>
</html>
```